Quarrybend Marble & Tile Needs a Business Card

Attached you will find your logo, my photo and design guidelines for a new business card. The final design will need two separate files to create an embossed card. The cards will be printed by www.plinkprint.com (Instructions below)
Format is the Plink SQUARE card
Quarrybend Marble And Tile is a brick and mortar, retail stone and tile shop.
One the front:
Quarrybend Marble And Tile
Dorian Fesslock
Owner
24807 Hollis Verdant Blvd
Suite P & R
Charlotte, NC 28193
Cell: 704-583-7142
Web: www.QuarrybendMarbleAndTile.com
(Make each word of the domain a different or alternating color)
On the back;
Something that shows beautiful colorful tile
Follow the design guide closely please. For more information see this page that describes creating the spot gloss file: https://www.plinkprint.com/us/business-cards/design-guidelines-spot-gloss
The logo is what we would like to have raised spot glossed.
Format is the Plink SQUARE card. See attahced guidlines.

```html
<!DOCTYPE html>
<html lang="en">
<head>
<meta charset="utf-8">
<title>Quarrybend Marble &amp; Tile – Business Card</title>
<link rel="stylesheet" href="https://fonts.googleapis.com/css2?family=Cinzel:wght@500&family=Noto+Sans:wght@400&display=swap">
<style>
  :root {
    --backdrop: #b7b7b7;
    --navy: #22323d;
    --navy-text: #1f2e3a;
    --gloss-blue: #3d8db5;
    --amber: #d08a2a;
    --white: #ffffff;
    --photo-tone: #c4b8a6;
    --tile-rust: #b04a2a;
    --tile-olive: #7a8062;
    --tile-gold: #d39a36;
  }
  * { margin: 0; padding: 0; box-sizing: border-box; }
  html, body { width: 1200px; height: 995px; overflow: hidden; }
  body { background: var(--backdrop); position: relative; font-family: "Noto Sans", sans-serif; }

  .card { position: absolute; top: 296px; width: 401px; height: 402px; overflow: hidden; }

  /* Back card */
  .card-back { left: 192px; background: var(--navy); }
  .card-back .brand { position: absolute; left: 24px; top: 140px; display: flex; align-items: center; gap: 18px; }
  .card-back .brand-mark { width: 70px; height: 70px; background: var(--gloss-blue); opacity: .55; }
  .card-back .brand-name { font-family: "Cinzel", serif; font-weight: 500; color: var(--gloss-blue); line-height: 1; }
  .card-back .brand-name .primary { display: block; font-size: 29px; letter-spacing: 3px; }
  .card-back .brand-name .secondary { display: block; font-size: 13px; letter-spacing: 6px; margin-top: 12px; }

  /* Front card */
  .card-front { left: 607px; background: var(--white); }
  .top-band { position: absolute; left: 0; top: 0; width: 100%; height: 5px; background: var(--amber); }
  .card-front .brand { position: absolute; left: 38px; top: 34px; display: flex; align-items: center; gap: 16px; }
  .card-front .brand-mark { width: 58px; height: 58px; background: var(--amber); }
  .card-front .brand-name { font-family: "Cinzel", serif; font-weight: 500; color: var(--navy-text); line-height: 1; }
  .card-front .brand-name .primary { display: block; font-size: 29px; letter-spacing: 3px; }
  .card-front .brand-name .secondary { display: block; font-size: 13px; letter-spacing: 6px; margin-top: 12px; }

  .portrait { position: absolute; left: 17px; top: 129px; width: 129px; height: 150px; border-radius: 10px; background: linear-gradient(180deg, var(--photo-tone) 0%, #b9ab98 60%, #3a4150 100%); }

  .contact { position: absolute; left: 163px; top: 128px; color: var(--navy-text); }
  .contact .person { font-family: "Cinzel", serif; font-weight: 500; font-size: 18px; letter-spacing: .3px; line-height: 22px; }
  .contact .role { color: var(--amber); font-size: 14px; line-height: 18px; }
  .contact .rule { width: 27px; height: 1px; background: var(--navy-text); margin: 9px 0 8px; }
  .contact .line { font-size: 14px; line-height: 21px; white-space: nowrap; }
  .contact .web { font-size: 12.6px; }
  .contact .accent { color: var(--amber); }

  .tile-band { position: absolute; left: 0; top: 310px; width: 100%; height: 92px; background: linear-gradient(90deg, var(--navy) 0%, var(--tile-rust) 25%, var(--tile-olive) 50%, var(--tile-gold) 75%, var(--navy) 100%); }
</style>
</head>
<body>
  <section class="card card-back">
    <div class="brand">
      <span class="brand-mark"></span>
      <span class="brand-name"><span class="primary">QUARRYBEND</span><span class="secondary">MARBLE &amp; TILE</span></span>
    </div>
  </section>

  <section class="card card-front">
    <div class="top-band"></div>
    <div class="brand">
      <span class="brand-mark"></span>
      <span class="brand-name"><span class="primary">QUARRYBEND</span><span class="secondary">MARBLE &amp; TILE</span></span>
    </div>

    <div class="portrait" role="img" aria-label="Portrait photo of the owner"></div>

    <div class="contact">
      <p class="person">DORIAN FESSLOCK</p>
      <p class="role">Owner</p>
      <div class="rule"></div>
      <p class="line">704-583-7142</p>
      <p class="line web">www.<span class="accent">Quarrybend</span>Marble<span class="accent">AndTile</span>.com</p>
      <div class="rule"></div>
      <p class="line">24807 Hollis Verdant Blvd,</p>
      <p class="line">Suite P &amp; R Charlotte, NC 28193</p>
    </div>

    <div class="tile-band" role="img" aria-label="Band of colourful geometric tile pattern"></div>
  </section>
</body>
</html>
```